Prosperity Pathway Basics PowerPoint

Please edit the following attached PowerPoint entitled workshop. Use the other attached PDF "TerraVesta Northern California Value Proposition" as a reference for the design and color I would like.

```html
<!DOCTYPE html>
<html lang="en">
<head>
<meta charset="utf-8">
<title>Prosperity Pathway Basics – Slide Set</title>
<link href="https://fonts.googleapis.com/css2?family=Exo+2:wght@400;500;600&family=Nunito+Sans:wght@400;600;700&display=swap" rel="stylesheet">
<style>
:root{
  --board:#8f8f8f;
  --navy:#0b2f7a;
  --blue:#1546a8;
  --deep:#061a4a;
  --pale:#eef3fc;
  --ink:#0d1730;
  --muted:#5c6578;
  --white:#ffffff;
  --red:#e32416;
}
*{margin:0;padding:0;box-sizing:border-box}
html,body{width:1200px;height:410px;overflow:hidden;background:var(--board)}
body{position:relative;font-family:"Nunito Sans",sans-serif;color:var(--ink)}
.slide{position:absolute;width:245px;height:137px;overflow:hidden;background:var(--pale)}
.s1{left:51px;top:51px}.s2{left:335px;top:51px}.s3{left:620px;top:51px}.s4{left:904px;top:51px}
.s5{left:51px;top:221px}.s6{left:335px;top:221px}.s7{left:620px;top:221px}.s8{left:904px;top:221px}
.abs{position:absolute}
.title{font-family:"Exo 2",sans-serif;font-weight:500;color:var(--ink);line-height:1.1}
.rule{position:absolute;height:1px;width:16px;background:var(--navy)}
.body{font-size:3.6px;line-height:1.45;color:var(--muted)}
.page{position:absolute;right:7px;bottom:6px;font-size:4.3px;color:var(--muted);letter-spacing:.1px}
.page b{font-weight:700;color:var(--navy)}
.brand{position:absolute;left:10px;bottom:6px;font-family:"Exo 2",sans-serif;color:var(--navy)}
.brand .name{display:flex;align-items:center;gap:2px;font-size:8.5px;font-weight:600;line-height:1}
.brand .name i{display:block;width:3.5px;height:3.5px;border-radius:50%;background:currentColor}
.brand .sub{font-size:4.2px;padding-left:10px;line-height:1.2;font-family:"Nunito Sans",sans-serif;font-weight:600}
.brand.light{color:var(--white)}
.photo{position:absolute}
.card{position:absolute;background:var(--white);border-radius:2px;box-shadow:0 1px 3px rgba(0,0,0,.12);text-align:center}
.card .rule{left:50%;margin-left:-18px}
.footer{position:absolute;bottom:10px;font-size:4.5px;color:var(--white)}
.s1 .photo{inset:0;background:linear-gradient(160deg,#2f5590 0%,#4f72a8 50%,#35588f 100%)}
.s1 .center{position:absolute;left:0;right:0;text-align:center;color:var(--white)}
.s2 .photo{left:0;top:0;width:108px;height:137px;background:linear-gradient(150deg,#0f3b8c 0%,#0a2a6a 55%,#07204f 100%)}
.s2 .icon{position:absolute;left:120px;width:20px;height:9px}
.loss-art{position:absolute;left:150px;top:55px;width:80px;height:46px;border-radius:3px;background:radial-gradient(ellipse at 55% 55%,rgba(227,36,22,.55) 0%,rgba(227,36,22,.18) 55%,rgba(227,36,22,0) 80%)}
.list{list-style:none;font-size:4.3px;color:var(--muted);line-height:1.75}
.list li::before{content:"→";color:var(--navy);margin-right:3px}
</style>
</head>
<body>

<section class="slide s1">
  <div class="photo" role="img" aria-label="Bridge over the bay with hills in soft blue light"></div>
  <div class="center" style="top:23px;font-family:'Exo 2',sans-serif;font-size:17px;font-weight:600;display:flex;justify-content:center;align-items:center;gap:4px"><span style="width:5px;height:5px;border-radius:50%;background:#fff;display:block"></span>TerraVesta</div>
  <div class="center" style="top:41px;font-size:8px;font-family:'Exo 2',sans-serif">Northern California</div>
  <div class="center" style="top:68px;font-family:'Exo 2',sans-serif;font-size:13px;font-weight:500">Presentation Title Goes Here</div>
  <div class="center" style="top:86px;font-size:6px;opacity:.9">Credential Subtitle Presentation</div>
  <div class="footer" style="left:10px">www.northerncalifornia.terravesta.com</div>
  <div class="footer" style="right:10px">June 2024</div>
</section>

<section class="slide s2">
  <div class="photo" role="img" aria-label="Stock market candlestick chart in deep blue"></div>
  <div class="rule" style="left:10px;top:9px;background:#fff"></div>
  <div class="abs title" style="left:10px;top:12px;font-size:10.5px;color:#fff">Your Money</div>
  <svg class="icon" style="top:19px" viewBox="0 0 20 9"><path d="M0 1h15a4 4 0 0 1 0 8H4L0 5z" fill="#0b2f7a"/><circle cx="14" cy="5" r="2.6" fill="none" stroke="#fff" stroke-width=".6"/><path d="M13.4 3.9l1.2 1.1-1.2 1.1" fill="none" stroke="#fff" stroke-width=".6"/></svg>
  <div class="abs title" style="left:144px;top:18px;font-size:8.5px">Objective</div>
  <div class="abs" style="left:144px;top:29px;font-size:5.8px;color:var(--muted)">Build as big as possible</div>
  <svg class="icon" style="top:46px" viewBox="0 0 20 9"><path d="M0 1h15a4 4 0 0 1 0 8H4L0 5z" fill="#0b2f7a"/><circle cx="14" cy="5" r="2.6" fill="none" stroke="#fff" stroke-width=".6"/><path d="M13.4 3.9l1.2 1.1-1.2 1.1" fill="none" stroke="#fff" stroke-width=".6"/></svg>
  <div class="abs title" style="left:144px;top:45px;font-size:8.5px">How</div>
  <div class="abs" style="left:144px;top:56px;font-size:5.8px;line-height:1.45;color:var(--muted)">Higher rates of return?<br>More risk?<br>"Better" products?</div>
  <div class="abs" style="left:120px;top:89px;font-size:5.4px;line-height:1.45;font-weight:700;color:var(--navy)">Having an efficient overall strategy is the key;<br>it all starts here!</div>
  <div class="brand light"><div class="name"><i></i>TerraVesta</div><div class="sub">Northern California</div></div>
  <div class="page">PAGE | <b>02</b></div>
</section>

<section class="slide s3">
  <div class="rule" style="left:10px;top:11px"></div>
  <div class="abs title" style="left:10px;top:14px;font-size:11px">Why is Your Strategy so Important ?</div>
  <div class="abs body" style="left:10px;top:40px;width:165px">We all only have a finite amount of money...we have to be efficient with it in the short time we have.<br>Inefficiencies cause major losses to occur.</div>
  <div class="abs" style="left:10px;top:60px;font-size:5.4px;color:var(--ink)">These losses can be reflected in:</div>
  <ul class="abs list" style="left:10px;top:71px"><li>Lower current lifestyle</li><li>Lower retirement income</li><li>Inadequate protection</li><li>Loss of financial control</li></ul>
  <ul class="abs list" style="left:81px;top:71px"><li>Financial vulnerability</li><li>Higher taxes and fees</li><li>Less benefits</li></ul>
  <div class="loss-art" role="img" aria-label="Red falling arrow with a percent sign showing losses"></div>
  <div class="brand"><div class="name"><i></i>TerraVesta</div><div class="sub">Northern California</div></div>
  <div class="page">PAGE | <b>03</b></div>
</section>

<section class="slide s4">
  <div class="photo" style="left:0;top:0;width:245px;height:63px;background:linear-gradient(160deg,#0a2a6c,#1a4aa5 60%,#123a8a)" role="img" aria-label="Blue financial bar chart backdrop"></div>
  <div class="card" style="left:16px;top:46px;width:212px;height:57px">
    <div class="rule" style="top:9px"></div>
    <div class="title" style="margin-top:12px;font-size:11px">How Significant is Efficiency?</div>
    <div class="body" style="margin:6px 12px 0">An individual might be able to create $75,000/year (1 unit) of retirement income based on current savings with an inefficient process. The same individual could create $125,000/year of retirement income with an efficient process using the same amount of savings.</div>
  </div>
  <div class="brand"><div class="name"><i></i>TerraVesta</div><div class="sub">Northern California</div></div>
  <div class="page">PAGE | <b>04</b></div>
</section>

<section class="slide s5">
  <div class="rule" style="left:37px;top:8px"></div>
  <div class="abs title" style="left:0;right:0;top:11px;text-align:center;font-size:11px">Dual Economic Forces™ Approach</div>
  <div class="abs body" style="left:8px;top:40px;width:105px">An individual might be able to create $75,000/year (1 unit) of retirement income based on current savings with an inefficient process. The same individual could create $125,000/year of retirement income with an efficient process using the same amount of savings.</div>
  <div class="abs body" style="left:128px;top:40px;width:108px">Equally important is that not only was there a transfer of risk/responsibility that occurred, but in a Defined Contribution Plan the employee is no longer getting both economic forces by default... they are getting the Interest Rates/Rates of Return force, but they must now seek out and understand how to incorporate the Actuarial Science force as they are not getting it by default.<br><br>These forces were meant to work together in balance and coordination to achieve efficient results.</div>
  <div class="brand"><div class="name"><i></i>TerraVesta</div><div class="sub">Northern California</div></div>
  <div class="page">PAGE | <b>05</b></div>
</section>

<section class="slide s6">
  <div class="photo" style="left:173px;top:0;width:72px;height:137px;background:linear-gradient(160deg,#0c3a96,#0a2a70 50%,#061c4c)" role="img" aria-label="Glowing blue line chart on a grid"></div>
  <div class="rule" style="left:9px;top:11px"></div>
  <div class="abs title" style="left:9px;top:14px;font-size:11px;line-height:1.15">The Cornerstones of<br>Financial<br>Stability and Wealth Building</div>
  <div class="abs body" style="left:9px;top:60px;width:140px">The decision for which option or combination of options to use for retirement income is made at the time of retirement. No matter which Cornerstones option(s) you choose you are much better off than being limited to the uncertainty of an invested retirement asset only strategy for retirement income. It is vital to have these two Cornerstones working together giving you the ability to create potentially higher, more secure retirement income streams. The Cornerstones also provide you with many Pre-Retirement benefits along the way.</div>
  <div class="brand"><div class="name"><i></i>TerraVesta</div><div class="sub">Northern California</div></div>
  <div class="page" style="color:#fff">PAGE | <b style="color:#fff">06</b></div>
</section>

<section class="slide s7">
  <div class="photo" style="left:0;top:60px;width:245px;height:77px;background:linear-gradient(180deg,#0a2462,#06183f 70%,#0b2e75)" role="img" aria-label="Glowing blue candlestick chart on a dark grid"></div>
  <div class="card" style="left:16px;top:19px;width:212px;height:57px">
    <div class="rule" style="top:9px"></div>
    <div class="title" style="margin-top:12px;font-size:11px">Option #2 - Volatility Buffer</div>
    <div class="body" style="margin:6px 18px 0">Let's take a look at an example illustrating the effectiveness of the Volatility Buffer when withdrawing high income rates from invested money</div>
  </div>
  <div class="brand light"><div class="name"><i></i>TerraVesta</div><div class="sub">Northern California</div></div>
  <div class="page" style="color:#fff">PAGE | <b style="color:#fff">07</b></div>
</section>

<section class="slide s8">
  <div class="photo" style="inset:0;background:linear-gradient(180deg,#1b3f83,#24498c 45%,#162f62)" role="img" aria-label="City skyline and bridge at dusk in blue tones"></div>
  <div class="abs title" style="left:0;right:0;top:23px;text-align:center;font-size:10px;color:#fff">Thank You !</div>
  <div class="abs" style="left:63px;top:40px;width:119px;height:1px;background:#fff"></div>
  <div class="abs body" style="left:18px;right:18px;top:48px;text-align:center;color:#fff">An individual might be able to create $75,000/year (1 unit) of retirement income based on current savings with an inefficient process. The same individual could create $125,000/year of retirement income with an efficient</div>
  <svg class="abs" style="left:76px;top:68px" width="94" height="12" viewBox="0 0 94 12" aria-label="Social links"><g fill="none" stroke="#fff" stroke-width=".7"><circle cx="6" cy="6" r="5"/><circle cx="26" cy="6" r="5"/><circle cx="46" cy="6" r="5"/><circle cx="66" cy="6" r="5"/><circle cx="86" cy="6" r="5"/></g></svg>
  <div class="abs" style="left:0;right:0;top:90px;display:flex;flex-direction:column;align-items:center;color:#fff;font-family:'Exo 2',sans-serif">
    <div style="display:flex;align-items:center;gap:2px;font-size:10px;font-weight:600;line-height:1"><span style="width:4px;height:4px;border-radius:50%;background:#fff;display:block"></span>TerraVesta</div>
    <div style="font-size:4.8px;font-family:'Nunito Sans',sans-serif">Northern California</div>
  </div>
  <div class="footer" style="left:10px">www.northerncalifornia.terravesta.com</div>
  <div class="footer" style="right:10px">June 2024</div>
</section>

</body>
</html>
```